Audio-Visual & Video Communications Business Requires a Cutting-edge Business Card Design

LinkVerra is a new Audio-Visual & Video Communications company in Cape Town, South Africa that is looking for a cutting-edge business card design. We sell these products to the Corporate, Education & Hospitality markets and will also host an Online Shop for companies and individuals to purchase our products online.

We are already using the following two colours in our logo and draft website. Please incorporate these colours into the design. Please note that our website is still in the design stage if you need to visit it. Green #a0ce4e & Dark Grey #333333.

Hi,

Please note that I have uploaded our logo in an .eps format.

Target Market(s)

Corporate Companies, Education Institutions & Hospitality Markets

Industry/Entity Type

Business

Requirements
Nice to have
• It would be great if you could incorporate the services that we offer.

1. Consultation & Design
2. Project Management
3. Supply & Installation
4. Onsite Support Personal
5. Online Shop

```html
<!DOCTYPE html>
<html lang="en">
<head>
<meta charset="utf-8">
<title>LinkVerra Business Card</title>
<link rel="stylesheet" href="https://fonts.googleapis.com/css2?family=Open+Sans:wght@400;600;700&display=swap">
<style>
  :root {
    --green: #a0ce4e;
    --dark-grey: #333333;
    --text-grey: #555555;
    --card-grey: #5b5b5b;
    --card-white: #ffffff;
    --page-bg: #e4e8ea;
  }
  * { box-sizing: border-box; margin: 0; padding: 0; }
  html, body {
    width: 1200px;
    height: 960px;
    overflow: hidden;
  }
  body {
    background: var(--page-bg);
    font-family: "Open Sans", Arial, sans-serif;
    position: relative;
  }
  .card {
    position: absolute;
    left: 240px;
    width: 720px;
    height: 412px;
    border-radius: 4px;
    box-shadow: 0 6px 18px rgba(0,0,0,0.15);
    overflow: hidden;
  }
  .card-front { top: 44px; background: var(--card-white); }
  .card-back  { top: 504px; background: var(--card-grey); }

  /* Front */
  .brand {
    position: absolute;
    left: 52px;
    top: 64px;
    display: flex;
    align-items: center;
    gap: 16px;
  }
  .brand-dot {
    width: 54px;
    height: 54px;
    border-radius: 50%;
    background: var(--green);
  }
  .brand-name {
    font-weight: 700;
    font-size: 46px;
    color: var(--green);
    letter-spacing: -0.5px;
  }
  .person {
    position: absolute;
    left: 52px;
    top: 236px;
    color: var(--text-grey);
  }
  .person-name {
    font-size: 30px;
    font-weight: 400;
    letter-spacing: 1px;
  }
  .person-title {
    font-size: 20px;
    margin-top: 2px;
  }
  .website {
    position: absolute;
    left: 52px;
    bottom: 48px;
    font-size: 20px;
    font-weight: 600;
    color: var(--green);
    letter-spacing: 0.5px;
  }
  .contact {
    position: absolute;
    left: 420px;
    top: 218px;
    font-size: 16px;
    color: var(--text-grey);
    line-height: 1.5;
  }
  .contact-label { color: var(--green); margin-right: 6px; }
  .address { margin-top: 36px; }

  /* Back */
  .back-name {
    position: absolute;
    left: 62px;
    top: 58px;
    font-weight: 700;
    font-size: 40px;
    color: var(--green);
    letter-spacing: 1.5px;
  }
  .services {
    position: absolute;
    left: 62px;
    top: 144px;
    list-style: none;
  }
  .services li {
    font-size: 19px;
    color: #f2f2f2;
    letter-spacing: 2px;
    line-height: 1.45;
    display: flex;
    align-items: center;
  }
  .services li::before {
    content: "";
    width: 6px;
    height: 6px;
    border-radius: 50%;
    background: var(--green);
    margin-right: 12px;
    flex-shrink: 0;
  }
</style>
</head>
<body>
  <section class="card card-front">
    <div class="brand">
      <span class="brand-dot"></span>
      <span class="brand-name">LinkVerra</span>
    </div>
    <div class="person">
      <p class="person-name">MARA QUINLAN</p>
      <p class="person-title">Manager</p>
    </div>
    <p class="website">www.linkverra.com</p>
    <div class="contact">
      <p><span class="contact-label">t</span>021.555.0147</p>
      <p><span class="contact-label">e</span>support@linkverra.com</p>
      <p class="address">PO Box 2207, Rondebosch, Cape Town<br>7700, South Africa.</p>
    </div>
  </section>

  <section class="card card-back">
    <p class="back-name">LinkVerra</p>
    <ul class="services">
      <li>Consultation &amp; Design</li>
      <li>Project Management</li>
      <li>Supply &amp; Installation</li>
      <li>Onsite Support Personal</li>
      <li>Online Shop</li>
    </ul>
  </section>
</body>
</html>
```